Design the Business card for NetVaultic

Business card required for a professional Cyber Security business.
Company Logo and Icon has already been provided however I would like other options for the logo and icon to compare to. Alternatively, please refine/enhance the image of the logo.icon I have already provided.

If you are going to use the provided logo and icon, I was thinking that the company raised Logo on White background would serve well on the front of the card. See attached. AND, a large company raised stand-alone icon to appear on black background on the back of the card with tagline 'Cyber Risk Management, Governance and Consulting' or 'Cyber Security for your Business' See attached.
Alternatively, provide your own design for the logo and icon.

Target Market(s)

Enterprise, Government, Financial.

Contact Information for Business Card

Tavin Orloweth
Founder and CEO

Email Address
Mobile Number
Website URL
LinkedIn URL

Logo Text

NetVaultic - see attached example of logo

Font styles to use
Other font styles liked:
• Berlin Sans FB

Requirements
Must have
• Clean large and bold icon on the back with tagline.
• Horizontal alignment,
Nice to have
• Round edges.
• Raised Logo/Icon
Should not have
• An unprofessional look and feel.

```html
<!DOCTYPE html>
<html lang="en">
<head>
<meta charset="utf-8">
<title>NetVaultic Business Card</title>
<link rel="stylesheet" href="https://fonts.googleapis.com/css2?family=Varela+Round&family=Roboto:wght@400&display=swap">
<style>
  :root {
    --stage: #2b2b2c;
    --card-white: #f4f4f4;
    --card-white-edge: #e9e9e9;
    --card-black: #1c1d1f;
    --brand-blue: #1e73be;
    --soft-blue: #4a72c4;
    --pale-blue: #dbe4f5;
    --brand-yellow: #f5b400;
    --ink: #444446;
  }
  html, body {
    margin: 0;
    padding: 0;
    width: 1200px;
    height: 960px;
    overflow: hidden;
    background: var(--stage);
  }
  .stage {
    position: relative;
    width: 1200px;
    height: 960px;
  }
  .card {
    position: absolute;
    width: 600px;
    height: 342px;
    box-shadow: 0 3px 8px rgba(0,0,0,0.5);
  }
  .card-front {
    left: 314px;
    top: 113px;
    background: radial-gradient(ellipse at 40% 40%, var(--card-white), var(--card-white-edge));
  }
  .card-back {
    left: 311px;
    top: 473px;
    background: var(--card-black);
  }
  .holder {
    position: absolute;
    left: 46px;
    top: 171px;
    font-family: "Varela Round", sans-serif;
  }
  .holder-name {
    margin: 0;
    font-size: 20px;
    color: var(--brand-blue);
    line-height: 24px;
    -webkit-text-stroke: 0.3px var(--brand-blue);
  }
  .holder-role {
    margin: 0;
    font-size: 14px;
    color: var(--brand-yellow);
    line-height: 18px;
  }
  .contact-list {
    position: absolute;
    left: 46px;
    top: 227px;
    margin: 0;
    padding: 0;
    list-style: none;
    font-family: "Roboto", sans-serif;
    font-size: 14px;
    color: var(--ink);
  }
  .contact-list li {
    display: flex;
    align-items: center;
    height: 19px;
  }
  .contact-list svg {
    width: 13px;
    height: 13px;
    margin-right: 10px;
    flex: none;
  }
  .front-mark {
    position: absolute;
    left: 278px;
    top: 12px;
    width: 306px;
    height: 322px;
    filter: drop-shadow(2px 5px 5px rgba(0,0,0,0.25));
  }
  .back-brand {
    position: absolute;
    left: 124px;
    top: 116px;
    display: flex;
    align-items: center;
  }
  .back-brand .brand-dot {
    width: 84px;
    height: 84px;
    border-radius: 50%;
    background: var(--soft-blue);
    margin-right: 10px;
  }
  .back-brand .brand-name {
    font-family: "Varela Round", sans-serif;
    font-size: 52px;
    color: var(--brand-blue);
    -webkit-text-stroke: 0.6px var(--brand-blue);
  }
  .tagline {
    position: absolute;
    left: 0;
    right: 0;
    top: 276px;
    margin: 0;
    text-align: center;
    font-family: "Varela Round", sans-serif;
    font-size: 17px;
    -webkit-text-stroke: 0.3px currentColor;
  }
  .tagline .risk { color: var(--soft-blue); }
  .tagline .governance { color: var(--brand-yellow); }
</style>
</head>
<body>
<main class="stage">
  <section class="card card-front">
    <div class="holder">
      <p class="holder-name">Tavin Orloweth</p>
      <p class="holder-role">Founder &amp; CEO</p>
    </div>
    <ul class="contact-list">
      <li>
        <svg viewBox="0 0 13 13"><rect x="3" y="0.5" width="7" height="12" rx="1.2" fill="none" stroke="var(--brand-blue)" stroke-width="1.6"/><circle cx="6.5" cy="10.5" r="0.8" fill="var(--brand-blue)"/></svg>
        555 014 2290
      </li>
      <li>
        <svg viewBox="0 0 13 13"><rect x="0.5" y="3" width="12" height="8" fill="var(--brand-blue)"/><path d="M0.5 3 L6.5 7.5 L12.5 3" fill="none" stroke="#fff" stroke-width="1"/></svg>
        tavin@netvaultic.com
      </li>
      <li>
        <svg viewBox="0 0 13 13"><circle cx="6.5" cy="6.5" r="6" fill="var(--brand-blue)"/><ellipse cx="6.5" cy="6.5" rx="2.6" ry="6" fill="none" stroke="#fff" stroke-width="0.9"/><line x1="0.5" y1="6.5" x2="12.5" y2="6.5" stroke="#fff" stroke-width="0.9"/></svg>
        www.netvaultic.com
      </li>
      <li>
        <svg viewBox="0 0 13 13"><circle cx="6.5" cy="6.5" r="6" fill="var(--brand-blue)"/></svg>
        netvaultic
      </li>
    </ul>
    <svg class="front-mark" viewBox="0 0 306 322" role="img" aria-label="Large raised NetVaultic brand mark">
      <defs>
        <radialGradient id="markTone" cx="50%" cy="45%" r="55%">
          <stop offset="0" stop-color="var(--soft-blue)"/>
          <stop offset="0.7" stop-color="#7d98d6"/>
          <stop offset="1" stop-color="var(--pale-blue)"/>
        </radialGradient>
      </defs>
      <circle cx="153" cy="161" r="148" fill="url(#markTone)"/>
    </svg>
  </section>

  <section class="card card-back">
    <div class="back-brand">
      <span class="brand-dot"></span>
      <span class="brand-name">NetVaultic</span>
    </div>
    <p class="tagline"><span class="risk">Cyber Risk Management,</span> <span class="governance">Governance &amp; Consulting</span></p>
  </section>
</main>
</body>
</html>
```